i would like a business card to leave with customers and potential customers for electrical work and for the supply and install of reverse cycle airconditioning in the domestic and commercial market.
I own my own business and im a sole trader. I have an a'class electrical lisence and also a refrigeration lisence so i am
able to offer complete installations in airconditioning by a fully qualified and lisenced tradesman.
im looking for something that comes across as unique and professional.
i had the coluor black and some gold in mind but open to any coluors.
something like Lanterra Electrical & Refrigeration
or Lanterra Air.
i will use this design on a business card to advertise through summer to help generate installs through the busy season.

Target Market(s)

Mainly domestic house holds through summer who are in need of airconditioning and reliable information to acomadate thier cooling and heating requirements

Industry/Entity Type

Electrical

Requirements
Must have
• Business name- Lanterra
My name- Mark Delford
My mobile no- 0438 517 290
My email- mrdelford@qelvo.com.au
Installation & Decomissioning of aiconditioning split systems
LIC NO: TRK 540316
Nice to have
• Lanterra Electrical & Refrigeration

```html
<!DOCTYPE html>
<html lang="en">
<head>
<meta charset="utf-8">
<title>Lanterra Electrical &amp; Refrigeration — Business Card</title>
<link rel="stylesheet" href="https://fonts.googleapis.com/css2?family=Archivo:wght@800&family=Open+Sans:ital,wght@0,400;0,700;1,400&display=swap">
<style>
  :root {
    --backdrop: #a9cde3;
    --card-light: #f7f7f7;
    --card-mid: #e4e4e4;
    --card-edge: #cfcfcf;
    --accent-blue: #4aaad6;
    --brand-blue-light: #3fa6dc;
    --brand-blue-dark: #2b6ea6;
    --name-grey: #3d3d3d;
    --info-grey: #a3a3a3;
    --emboss-light: #f4f4f4;
    --emboss-shade: #c8c8c8;
  }
  * { margin: 0; padding: 0; box-sizing: border-box; }
  html, body {
    width: 1200px;
    height: 857px;
    overflow: hidden;
    background: var(--backdrop);
  }
  .canvas {
    position: relative;
    width: 1200px;
    height: 857px;
  }
  .card {
    position: absolute;
    left: 302px;
    width: 614px;
    height: 338px;
    border-radius: 26px;
    overflow: hidden;
    background: radial-gradient(ellipse at 45% 40%, var(--card-light) 0%, var(--card-mid) 70%, var(--card-edge) 100%);
  }
  .card--front { top: 60px; }
  .card--back { top: 464px; }

  .accent-bar {
    position: absolute;
    background: var(--accent-blue);
  }
  .accent-bar--top {
    left: 371px;
    top: 33px;
    width: 243px;
    height: 19px;
    border-radius: 10px 0 0 10px;
  }
  .accent-bar--bottom {
    left: 0;
    top: 240px;
    width: 257px;
    height: 31px;
  }

  .brand {
    position: absolute;
    left: 24px;
    top: 28px;
    font-family: "Archivo", Arial, sans-serif;
    font-weight: 800;
    font-size: 23px;
    line-height: 26px;
    letter-spacing: 0.5px;
    text-transform: uppercase;
  }
  .brand__line { display: block; }
  .brand__line--primary { color: var(--brand-blue-light); }
  .brand__line--secondary { color: var(--brand-blue-dark); padding-left: 47px; }

  .holder {
    position: absolute;
    right: 83px;
    top: 186px;
    text-align: right;
    font-family: "Open Sans", Arial, sans-serif;
    font-style: italic;
    color: var(--name-grey);
  }
  .holder__name { font-size: 29px; line-height: 34px; letter-spacing: -0.5px; }
  .holder__title { font-size: 16px; line-height: 18px; padding-right: 12px; }

  .contact {
    position: absolute;
    left: 31px;
    top: 104px;
    list-style: none;
    font-family: "Open Sans", Arial, sans-serif;
    font-size: 20px;
    line-height: 30px;
    color: var(--info-grey);
  }
  .contact__label { display: inline-block; width: 30px; }

  .licence {
    position: absolute;
    left: 0;
    top: 240px;
    width: 257px;
    height: 31px;
    font-family: "Open Sans", Arial, sans-serif;
    font-weight: 700;
    font-size: 15px;
    line-height: 31px;
    text-align: center;
    color: #ffffff;
    letter-spacing: 0.3px;
  }

  .services {
    position: absolute;
    left: 0;
    right: 0;
    top: 281px;
    text-align: center;
    font-family: "Archivo", Arial, sans-serif;
    font-weight: 800;
    font-size: 19px;
    line-height: 27px;
    letter-spacing: 2px;
    text-transform: uppercase;
    color: var(--emboss-light);
    text-shadow: 1px 1px 1px var(--emboss-shade);
  }
</style>
</head>
<body>
<main class="canvas">
  <section class="card card--front" aria-label="Card front">
    <h1 class="brand">
      <span class="brand__line brand__line--primary">Lanterra Electrical</span>
      <span class="brand__line brand__line--secondary">&amp; Refrigeration</span>
    </h1>
    <div class="accent-bar accent-bar--top"></div>
    <div class="holder">
      <p class="holder__name">Mark Delford</p>
      <p class="holder__title">Director</p>
    </div>
    <div class="accent-bar accent-bar--bottom"></div>
  </section>

  <section class="card card--back" aria-label="Card back">
    <div class="accent-bar accent-bar--top"></div>
    <ul class="contact">
      <li><span class="contact__label">P:</span> 0438 517 290</li>
      <li><span class="contact__label">E:</span> mrdelford@qelvo.com.au</li>
      <li><span class="contact__label">W:</span> www.lanterraair.com.au</li>
    </ul>
    <div class="accent-bar accent-bar--bottom"></div>
    <p class="licence">LIC NO: TRK 540316</p>
    <p class="services">Installation &amp; Decomissioning<br>of Airconditioning Split Systems</p>
  </section>
</main>
</body>
</html>
```